Online Advice via Video Site requires Cutting Edge Homepage

We need a creative new and exciting webdesign for our tutoring via video-chat website.

We have prepared a "demo" homepage for you to see various promotional material that we think would be suitable for the homepage. http://www.quillmarsh.com/demo

The actual site is undergoing some final tinkering but can be accessed and used at http://www.quillmarsh.com

There is NO NEED to take any colours or design structure from this.

We expect the logo to be changed to match the new site. The new logo should match the site's function.

I have included some other projects that we like the look of:
http://www.vantoplex.com.au/design/143762
http://www.vantoplex.com.au/design/561630
http://www.vantoplex.com.au/design/247199
http://www.vantoplex.com.au/design/255195
http://www.birchlume.tv/

Target Market(s)

People that will work as tutors/advisers or be student/clients

Industry/Entity Type

Tutoring

Requirements
Must have
• The search is the main feature of the homepage

After the search the next goal of the page is to get people to sign up to the site

Login, (optional inclusion of the gablenet login - if you don't include it then you need only have a "login" button... no username or password input fields)

Footer
Nice to have
• The promotional material for the site, the colours on the Prezi file CAN BE changed to suit the new design you propose.

```html
<!DOCTYPE html>
<html lang="en">
<head>
<meta charset="utf-8">
<title>Quill Marsh – Homepage</title>
<link rel="stylesheet" href="https://fonts.googleapis.com/css2?family=Source+Sans+3:wght@400;600&family=Open+Sans:wght@400;700&family=Arimo:wght@400&display=swap">
<style>
:root{
  --page:#f4f4f4;
  --panel:#f7f7f7;
  --line:#d6d6d6;
  --sky-top:#e4f6fa;
  --sky-bottom:#a7dbe7;
  --teal-top:#5b9fb1;
  --teal-bottom:#d3f0f6;
  --head-top:#69b3c4;
  --head-bottom:#c8ecf4;
  --blue:#1a47d6;
  --blue-dark:#1c3f9e;
  --text:#555;
  --muted:#7a7a7a;
  --white:#fff;
}
*{box-sizing:border-box;margin:0;padding:0}
html,body{width:1186px;height:1200px;overflow:hidden;background:var(--page)}
.stage{position:relative;width:1020px;height:1032px;transform:scale(1.1628);transform-origin:0 0;font-family:"Source Sans 3",sans-serif;color:var(--text)}
.abs{position:absolute}
.page-frame{left:32px;top:0;width:956px;height:1032px;background:var(--panel);border-left:1px solid var(--line);border-right:1px solid var(--line)}
.top-band{left:0;top:0;width:1020px;height:41px;background:linear-gradient(var(--sky-top),var(--sky-bottom))}
.brand{left:52px;top:8px;font-size:31px;color:#41618f;font-weight:400;letter-spacing:.5px}
.pill-btn{top:6px;height:28px;width:94px;display:flex;align-items:center}
.pill-btn .dot{width:30px;height:30px;border-radius:50%;background:var(--white);border:1px solid #b9c8d4;flex:none;z-index:1}
.pill-btn .label{margin-left:-8px;height:22px;flex:1;border-radius:11px;background:linear-gradient(#4f7bd0,#1d3f95);color:var(--white);font-size:13px;display:flex;align-items:center;justify-content:center;padding-left:6px}
.sep{left:862px;top:12px;width:1px;height:16px;background:#8fa7b4}
.card{background:#f1f1f1;border:1px solid var(--line);border-radius:3px}
.intro{left:42px;top:40px;width:462px;height:75px;padding:10px 12px;font-size:12.3px;line-height:16px;color:#5a5a5a}
.login{left:514px;top:40px;width:464px;height:76px}
.avatar{left:20px;top:11px;width:48px;height:52px;border-radius:6px;background:linear-gradient(#5f8fd0,#2e4e8c)}
.login-divider{left:80px;top:14px;width:1px;height:46px;background:#ccc}
.field{height:24px;border:1px solid #c5c5c5;border-radius:3px;background:linear-gradient(#e0e0e0,#f2f2f2);font-size:12px;font-style:italic;color:#888;padding:5px 8px}
.remember{left:101px;top:49px;font-size:12.5px;color:#777;display:flex;align-items:center;gap:6px}
.remember i{width:12px;height:12px;border:1px solid #2c55a5;display:block;background:var(--white)}
.forgot{left:216px;top:49px;font-size:12.5px;color:#777;padding-left:10px;border-left:1px solid #ccc}
.btn-small{height:24px;border:1px solid #c8d2dc;border-radius:2px;background:linear-gradient(#fff,#eaeaea);color:var(--blue);font-size:13px;display:flex;align-items:center;justify-content:center;gap:4px;font-family:"Arimo",sans-serif}
.search-band{left:32px;top:128px;width:956px;height:110px;background:linear-gradient(var(--teal-top),var(--teal-bottom) 70%,#e9f8fb)}
.search-bar{left:42px;top:145px;width:936px;height:43px;background:var(--white);border:1px solid #c8d8de;border-radius:3px}
.search-title{left:29px;top:11px;font-family:"Open Sans",sans-serif;font-weight:700;font-size:17px;color:var(--blue)}
.search-field{left:336px;top:9px;width:469px;height:25px}
.tagline{left:32px;top:198px;width:956px;text-align:center;font-size:20px;color:var(--blue);text-shadow:0 1px 0 #fff}
.panel{background:#f3f3f3;border:1px solid #dcdcdc;box-shadow:0 2px 6px rgba(0,0,0,.12)}
.panel-head{height:38px;background:linear-gradient(var(--head-top),var(--head-bottom));color:var(--white);font-size:19px;padding:7px 12px}
.main-panel{left:46px;top:255px;width:624px;height:428px}
.video{left:58px;top:50px;width:516px;height:322px;border:1px solid #1e4d55;background:linear-gradient(#3c3c3c 0%,#6f8d93 35%,#a7dfea 90%)}
.video-text{left:0;top:58px;width:100%;text-align:center;font-family:"Open Sans",sans-serif;font-weight:700;font-size:54px;line-height:76px;color:#e9e9e9;text-shadow:0 3px 2px rgba(0,0,0,.45)}
.video-bar{left:0;bottom:0;width:100%;height:32px;background:linear-gradient(#f5f5f5,#e2e2e2);border-top:1px solid #ccc;font-size:12.5px;color:#555;font-family:"Arimo",sans-serif}
.tabs{left:46px;top:706px;width:624px;height:217px}
.tab{position:absolute;left:0;width:236px;height:52px;padding:14px 13px;font-size:16px;color:#777;background:linear-gradient(#fbfbfb,#dedede);border-bottom:1px solid #fff}
.tab.active{background:linear-gradient(#4aa6ba,#c2eaf3);color:var(--blue-dark);height:56px;text-shadow:0 1px 0 #fff}
.tab-body{left:236px;top:0;width:388px;height:217px;background:var(--white);border:1px solid #ddd;text-align:center;font-size:20px;color:var(--blue);line-height:41px;padding-top:31px}
.side{left:699px;width:273px}
.side .panel-head{font-size:19px;text-transform:uppercase;padding:8px 12px}
.topic{height:30px;border-bottom:1px solid #ddd;font-size:14px;color:#666;padding:6px 14px;display:flex;gap:14px;align-items:center}
.topic svg{flex:none}
.benefits{font-family:"Arimo",sans-serif;font-size:12px;color:#666;line-height:20px;padding:4px 0 0 14px;list-style:none}
.benefits li::before{content:"●";font-size:7px;color:#888;margin-right:8px;vertical-align:2px}
.benefits .sub{padding-left:34px}
.social-tile{top:58px;width:46px;height:46px;border-radius:7px;display:flex;align-items:center;justify-content:center;color:var(--white);font-size:10px;font-family:"Arimo",sans-serif}
.footer{left:0;top:943px;width:1020px;height:89px;background:linear-gradient(var(--sky-bottom),var(--sky-top))}
.footer-nav{top:14px;width:100%;text-align:center;font-size:12.5px;color:var(--blue-dark);letter-spacing:.6px;font-family:"Open Sans",sans-serif}
.copyright{top:37px;width:100%;text-align:center;font-size:12px;color:#777;letter-spacing:.6px;font-family:"Open Sans",sans-serif}
</style>
</head>
<body>
<div class="stage">
  <div class="abs page-frame"></div>
  <div class="abs top-band"></div>
  <div class="abs brand">Quill Marsh</div>

  <div class="abs pill-btn" style="left:760px"><span class="dot"></span><span class="label">Log in</span></div>
  <div class="abs sep"></div>
  <div class="abs pill-btn" style="left:870px"><span class="dot"></span><span class="label">Join us</span></div>

  <div class="abs card intro">● QuillMarsh is the place for e-learning, mentoring &amp; professional advice ● It instantly connects people with knowledge and those who need it ● Connects people for ongoing advice or on off answers ● Ask questions and/or work exactly when it suits you</div>

  <div class="abs card login">
    <div class="abs avatar" role="img" aria-label="Member account icon"></div>
    <div class="abs login-divider"></div>
    <div class="abs field" style="left:100px;top:14px;width:160px">User Name</div>
    <div class="abs field" style="left:281px;top:14px;width:160px">Password</div>
    <div class="abs remember"><i></i>Remember me</div>
    <div class="abs forgot">Forgot it ???</div>
    <div class="abs btn-small" style="left:361px;top:43px;width:78px">
      <svg width="14" height="8" viewBox="0 0 14 8"><path d="M0 4h12M9 1l3 3-3 3" stroke="currentColor" fill="none" stroke-width="1.3"/></svg>Sign in</div>
  </div>

  <div class="abs search-band"></div>
  <div class="abs search-bar">
    <svg class="abs" style="left:280px;top:0" width="60" height="43"><path d="M0 43 C25 40 30 2 60 1 L60 0 L0 0 Z" fill="#eef6f8"/></svg>
    <div class="abs search-title">Search Topics &amp; Advisor</div>
    <div class="abs field search-field">Enter your topic or Advisor name</div>
    <div class="abs btn-small" style="left:833px;top:9px;width:78px">
      <svg width="14" height="8" viewBox="0 0 14 8"><path d="M0 4h12M9 1l3 3-3 3" stroke="currentColor" fill="none" stroke-width="1.3"/></svg>Search</div>
  </div>
  <div class="abs tagline">"Imagine if, whenever you had a problem you could instantly access the world's experts to solve it. Now you can!"</div>

  <section class="abs panel main-panel">
    <div class="panel-head">Quill Marsh</div>
    <div class="abs video">
      <div class="abs video-text">DO YOU KNOW<br>SOMETHING ???</div>
      <div class="abs video-bar">
        <svg class="abs" style="left:14px;top:8px" width="16" height="16"><path d="M1 0 L15 8 L1 16 Z" fill="#444"/></svg>
        <div class="abs" style="left:42px;top:0;width:1px;height:32px;background:#ccc"></div>
        <span class="abs" style="left:54px;top:8px">00:00</span>
        <div class="abs" style="left:92px;top:12px;width:293px;height:8px;background:#cfcfcf;border-radius:2px"></div>
        <div class="abs" style="left:137px;top:6px;width:9px;height:20px;background:#555;border-radius:3px"></div>
        <span class="abs" style="left:391px;top:8px">00:00</span>
        <svg class="abs" style="left:430px;top:8px" width="74" height="16">
          <path d="M1 5h4l5-4v14l-5-4H1z" fill="#444"/><path d="M12 4q3 4 0 8" stroke="#444" fill="none" stroke-width="1.5"/>
          <path d="M28 1h5M28 1v5M42 1h-5M42 1v5M28 15h5M28 15v-5M42 15h-5M42 15v-5" stroke="#444" stroke-width="2" fill="none"/>
          <path d="M60 3l-5 5 5 5M66 3l5 5-5 5" stroke="#444" stroke-width="2" fill="none"/>
        </svg>
      </div>
    </div>
  </section>

  <section class="abs tabs">
    <div class="tab active" style="top:0">Instant Personal Advice</div>
    <svg class="abs" style="left:236px;top:0" width="24" height="56"><path d="M0 0 L24 28 L0 56 Z" fill="#8fd0de"/></svg>
    <div class="tab" style="top:58px">Direct Video Conference</div>
    <div class="tab" style="top:111px">Advisors and/or Clients</div>
    <div class="tab" style="top:164px">Paylark Or Credit Card</div>
    <div class="abs tab-body">Find advisors<br>waiting online<br>OR<br>Book appointment when it suits</div>
  </section>

  <aside class="abs panel side" style="top:256px;height:232px">
    <div class="panel-head">Advisors by Topics</div>
    <div class="topic"><svg width="12" height="6"><path d="M0 3h10M8 1l2 2-2 2" stroke="#888" fill="none"/></svg>English</div>
    <div class="topic"><svg width="12" height="6"><path d="M0 3h10M8 1l2 2-2 2" stroke="#888" fill="none"/></svg>Building</div>
    <div class="topic"><svg width="12" height="6"><path d="M0 3h10M8 1l2 2-2 2" stroke="#888" fill="none"/></svg>Cultural Studies</div>
    <div class="topic"><svg width="12" height="6"><path d="M0 3h10M8 1l2 2-2 2" stroke="#888" fill="none"/></svg>Criminology</div>
    <div class="topic"><svg width="12" height="6"><path d="M0 3h10M8 1l2 2-2 2" stroke="#888" fill="none"/></svg>Agriculture</div>
    <div class="topic"><svg width="12" height="6"><path d="M0 3h10M8 1l2 2-2 2" stroke="#888" fill="none"/></svg>Veterinary Scienc</div>
  </aside>

  <aside class="abs panel side" style="top:500px;height:263px">
    <div class="panel-head">Professional Advisors</div>
    <ul class="benefits">
      <li>Provide advice in your profession</li>
      <li>Provide advice in various forms</li>
      <li class="sub">Solve one off issues</li>
      <li class="sub">Provide ongoing advice</li>
      <li class="sub">Conduct client meetings onsite</li>
      <li>Work when it suits you</li>
      <li>Pre-book appointments</li>
      <li class="sub">Answer questions only when you can</li>
      <li class="sub">Earn money for your time</li>
      <li>Set your own fee rate</li>
    </ul>
    <svg class="abs" style="left:224px;top:244px" width="34" height="10"><path d="M10 0 L0 5 L10 10Z M24 0 L34 5 L24 10Z" fill="#888"/></svg>
  </aside>

  <aside class="abs panel side" style="top:780px;height:143px">
    <div class="panel-head">Connect with us</div>
    <div class="abs social-tile" style="left:18px;background:#3f5e9c">gablenet</div>
    <div class="abs social-tile" style="left:82px;background:#4fb2d3">Chirpwell</div>
    <div class="abs social-tile" style="left:149px;background:#e08a1c">Feedline</div>
    <div class="abs social-tile" style="left:214px;background:#2b2b2b">Orbitplus</div>
  </aside>

  <footer class="abs footer">
    <nav class="abs footer-nav">Home | Student | Advisors | Topics | Blog | FAQs | Sitemap | About us | Our Technology | Contact</nav>
    <div class="abs copyright">Copyright @ 2012</div>
  </footer>
</div>
</body>
</html>
```